Digital Marketing Agency Landing Page

At VELIM, we offer a comprehensive solution for solar companies' client acquisition needs in the rapidly growing industry. We handle end-to-end client acquisition, meaning we manage the entire lifecycle of capturing new clients—from initial lead generation to delivering the ready-to-buy homeowner. Our expertise in targeted advertising, data analytics, and customer relationship management ensures that we not only find potential customers but also nurture them through tailored engagement strategies until they are ready to make a purchase. By entrusting us with your client acquisition process, solar companies can focus on what they do best—providing sustainable energy solutions—while we work behind the scenes to grow your customer base and increase your market share.

We need to restructure our website to make it more professional. We don't need any complex functionalities. We are looking for someone that is good in design and can build a visually aesthetic website following our brand image. We only need a landing page and a lead form in the end. I would like to have only one page, but a relatively big one where people scroll down. I would like to have a minimal and classy look. Something that is timeless and elegant.

Structure:

initial page
About us
How we operate
Get in touch

Target Market(s)

Solar Comapanies

Industry/Entity Type

Marketing solautions

Coding

Coded - Design and coding required

Number of Pages Required

1 page

Requirements
Nice to have
• Inspirations: https://www.qz.zu/ https://www.marchbeck.example/ https://www.tovanrid.example/ https://pruvo.example/

```html
<!DOCTYPE html>
<html lang="en">
<head>
<meta charset="utf-8">
<title>VELIM — Client Acquisition for Solar Companies</title>
<link rel="stylesheet" href="https://fonts.googleapis.com/css2?family=Montserrat:wght@300;400;500;600&display=swap">
<style>
:root{
  --navy:#0f2233;
  --navy-deep:#0c1c2b;
  --card:#1b3a52;
  --card-shadow:#142d42;
  --cream:#f3efe3;
  --frame:#e9e1cd;
  --text:#1c2a36;
  --white:#ffffff;
  --panel:rgba(232,232,234,.93);
}
*{box-sizing:border-box;margin:0;padding:0}
html,body{width:745px;height:1200px;overflow:hidden;background:var(--white)}
body{font-family:"Montserrat",sans-serif;color:var(--text);position:relative}
.abs{position:absolute}

/* Hero */
.hero{position:absolute;left:0;top:0;width:745px;height:442px;overflow:hidden}
.hero-photo{position:absolute;inset:0;background:
  radial-gradient(ellipse at 35% 35%,#6a5a4e 0%,transparent 55%),
  radial-gradient(ellipse at 75% 20%,#8a8580 0%,transparent 50%),
  linear-gradient(180deg,#5d6066 0%,#4e4a47 60%,#3b3835 100%)}
.hero-shade{position:absolute;inset:0;background:linear-gradient(90deg,rgba(20,25,35,.35),rgba(20,25,35,.1))}
.brand{left:47px;top:28px;color:var(--white);font-weight:500;font-size:24px;letter-spacing:1px;line-height:1}
.nav{left:418px;top:29px;display:flex;list-style:none}
.nav li{font-size:8.6px;color:var(--white);font-weight:500;letter-spacing:.3px;height:26px;display:flex;align-items:center}
.nav .active{border:1.3px solid var(--white);padding:0 10px}
.nav li+li{margin-left:20px}
.hero-title{left:44px;top:212px;color:var(--white);font-weight:400;font-size:71px;line-height:1;letter-spacing:1px}
.hero-lead{left:47px;top:281px;color:var(--white);font-size:16.3px;font-weight:500;line-height:21.8px;letter-spacing:.4px;white-space:nowrap}
.btn-cream{left:46px;top:363px;width:103px;height:37px;background:var(--cream);color:var(--text);font-size:9px;font-weight:500;letter-spacing:.5px;display:flex;align-items:center;justify-content:center}

.quick{left:493px;top:118px;width:206px;height:272px;background:var(--panel);padding:0 14px}
.quick h2{font-weight:500;font-size:16px;text-align:center;margin:15px 0 9px;color:var(--navy);letter-spacing:.3px}
.field{background:var(--white);height:30px;margin-bottom:6.5px;font-size:8.2px;font-weight:500;color:var(--text);padding:10px 10px 0}
.field.msg{height:70px;margin-bottom:7px}
.submit{height:30px;background:var(--navy);color:var(--white);font-size:12.5px;font-weight:500;display:flex;align-items:center;justify-content:center;letter-spacing:.3px}

/* About */
.about-frame{left:63px;top:506px;width:289px;height:229px;border:1.5px solid var(--frame)}
.about-photo{left:47px;top:490px;width:289px;height:227px;border:1.5px solid var(--frame);background:linear-gradient(135deg,#3e5878 0%,#9fb0c2 55%,#d9dde2 100%)}
.about-title{left:384px;top:485px;font-size:30px;font-weight:500;color:var(--navy);letter-spacing:1px}
.about-text{left:382px;top:527px;font-size:9.1px;line-height:16.6px;color:var(--text);white-space:nowrap;letter-spacing:.1px}
.about-text p+p{margin-top:6px}
.btn-outline{left:382px;top:699px;width:102px;height:32px;border:1px solid var(--navy);background:var(--cream);font-size:9px;font-weight:500;letter-spacing:.5px;display:flex;align-items:center;justify-content:center}
.btn-outline-shadow{left:387px;top:704px;width:102px;height:32px;border:1px solid var(--navy)}

/* Contact */
.contact{left:0;top:787px;width:745px;height:279px;background:linear-gradient(180deg,var(--navy) 0%,var(--navy-deep) 100%)}
.contact h2{position:absolute;left:0;right:0;top:53px;text-align:center;color:var(--white);font-size:29px;font-weight:500;letter-spacing:1.2px}
.card{width:204px;height:112px;background:var(--card);color:var(--white);text-align:center;top:109px;box-shadow:-5px 4px 0 var(--card-shadow)}
.card svg{display:block;margin:15px auto 0}
.card h3{font-size:12.5px;font-weight:500;letter-spacing:.6px;margin-top:6px}
.card p{font-size:10px;line-height:16.5px;margin-top:7px;letter-spacing:.2px}
.card p.big{font-size:12.5px;margin-top:8px;letter-spacing:.4px}

/* Footer */
.foot-nav{left:0;width:745px;top:1101px;display:flex;justify-content:center;gap:37px;list-style:none;font-size:10.3px;font-weight:500;letter-spacing:.5px;color:var(--text)}
.copy{left:0;width:745px;top:1127px;text-align:center;font-size:8.6px;letter-spacing:.2px}
.social{left:0;width:745px;top:1149px;display:flex;justify-content:center;gap:14px}
.social span{width:14px;height:14px;background:#2a2f36;border-radius:2px}
</style>
</head>
<body>

<header class="hero">
  <div class="hero-photo" role="img" aria-label="Photo of a smiling businessman at a meeting table with colleagues"></div>
  <div class="hero-shade"></div>
  <div class="abs brand">VELIM</div>
  <ul class="abs nav">
    <li class="active">HOME</li><li>ABOUT US</li><li>SERVICES</li><li>CONTACT US</li>
  </ul>
  <h1 class="abs hero-title">VELIM</h1>
  <p class="abs hero-lead">We offer a comprehensive solution for<br>solar companies' client acquisition needs in<br>the rapidly growing industry.</p>
  <div class="abs btn-cream">READ MORE</div>
  <form class="abs quick">
    <h2>QUICK CONTACT</h2>
    <div class="field">Name</div>
    <div class="field">Email Address</div>
    <div class="field">Phone No</div>
    <div class="field msg">Message</div>
    <div class="submit">Submit</div>
  </form>
</header>

<section>
  <div class="abs about-frame"></div>
  <div class="abs about-photo" role="img" aria-label="Photo of two colleagues shaking hands in a bright office"></div>
  <h2 class="abs about-title">ABOUT VELIM</h2>
  <div class="abs about-text">
    <p>Sed ut perspiciatis unde omnis iste natus error sit voluptatem<br>accusantium doloremque laudantium, totam rem aperiam, eaque<br>ipsa quae ab illo inventore veritatis et quasi architecto beatae vitae<br>dicta sunt explicabo. Nemo enim ipsam voluptatem quia voluptas<br>sit aspernatur aut odit aut fugit, sed quia consequuntur magni<br>dolores eos qui ratione voluptatem sequi nesciunt.</p>
    <p>Neque porro quisquam est, qui dolorem ipsum quia dolor sit<br>amet, consectetur, adipisci velit, sed quia non numquam eius<br>modi tempora incidunt ut labore et dolore.</p>
  </div>
  <div class="abs btn-outline-shadow"></div>
  <div class="abs btn-outline">READ MORE</div>
</section>

<section class="abs contact">
  <h2>CONTACT US</h2>
  <div class="abs card" style="left:46px">
    <svg width="15" height="20" viewBox="0 0 15 20"><path d="M7.5 0C3.4 0 0 3.3 0 7.4 0 12.5 7.5 20 7.5 20S15 12.5 15 7.4C15 3.3 11.6 0 7.5 0zm0 10.3a2.8 2.8 0 1 1 0-5.6 2.8 2.8 0 0 1 0 5.6z" fill="#fff"/></svg>
    <h3>ADDRESS</h3>
    <p>48 Harlow Quay, Suite 12,<br>Brindale 20417</p>
  </div>
  <div class="abs card" style="left:271px">
    <svg width="16" height="20" viewBox="0 0 16 20" style="margin-top:19px"><path d="M3 2l3 0 1.2 4-1.8 1.3c.9 2.2 2.3 3.9 3.9 5l1.6-1.5 3.2 2-.8 3.2c-5.2-.5-9.8-6.3-9.6-12.5z" fill="#fff" transform="translate(-1,1)"/><path d="M10 3a4 4 0 0 1 3 3M11 0.5a6.5 6.5 0 0 1 4.5 4.5" stroke="#fff" stroke-width="1.2" fill="none"/></svg>
    <h3>PHONE</h3>
    <p class="big">+1 555-014-7720</p>
  </div>
  <div class="abs card" style="left:496px">
    <svg width="19" height="14" viewBox="0 0 19 14" style="margin-top:22px"><rect width="19" height="14" rx="2" fill="#fff"/><path d="M1 2l8.5 6L18 2" stroke="#1b3a52" stroke-width="1.6" fill="none"/></svg>
    <h3>EMAIL</h3>
    <p class="big">hello@velimreach.example</p>
  </div>
</section>

<footer>
  <ul class="abs foot-nav"><li>HOME</li><li>ABOUT US</li><li>SERVICES</li><li>CONTACT US</li></ul>
  <p class="abs copy">© 2023 Company Name.&nbsp; All Rights Reserved.</p>
  <div class="abs social">
    <span aria-label="Social link"></span><span aria-label="Social link"></span><span aria-label="Social link"></span><span aria-label="Social link"></span><span aria-label="Social link"></span>
  </div>
</footer>

</body>
</html>
```